Local Roofing/Construction company business needs new biz card design

We need a new business card design, current cards are from the start of this operation and generic at best. We are a local Construction Company (General Contractor) with a majority of our work originating from insurance claims-exterior finish work is the main focus (Roofs-Siding-Gutters etc). Heavily involved with homeowners and the low ball offers they receive from insurance company's after a insurable event takes place. I have attached some of our original logo file(s) below.

```html
<!DOCTYPE html>
<html lang="en">
<head>
<meta charset="utf-8">
<title>Ironvale Construction – Business Card</title>
<link rel="stylesheet" href="https://fonts.googleapis.com/css2?family=Montserrat:wght@400;500;700;800&display=swap">
<style>
  :root {
    --bg: #2a2a2c;
    --card: #1f1f20;
    --card-black: #0d0d0e;
    --green: #2fd47a;
    --white: #f4f4f2;
    --muted: #d8d8d8;
  }
  * { box-sizing: border-box; margin: 0; padding: 0; }
  html, body { width: 1200px; height: 900px; overflow: hidden; }
  body {
    background: var(--bg);
    font-family: "Montserrat", sans-serif;
    position: relative;
  }
  .card {
    position: absolute;
    left: 270px;
    width: 660px;
    height: 378px;
    border-radius: 22px;
    overflow: hidden;
    border-bottom: 5px solid var(--green);
    box-shadow: 0 14px 30px rgba(0,0,0,0.45);
  }
  .card-back { top: 40px; background: var(--card-black); }
  .pattern-field {
    position: absolute; inset: 0;
    background:
      linear-gradient(115deg, rgba(200,200,200,0.85) 0%, rgba(120,120,120,0.6) 24%, rgba(50,50,50,0.4) 48%, rgba(20,20,20,0.2) 70%, rgba(10,10,10,0) 100%),
      var(--card-black);
  }
  .back-brand {
    position: absolute;
    right: 90px; top: 118px;
    display: flex; align-items: center; gap: 12px;
    color: var(--green);
    font-weight: 800;
    font-size: 30px;
    letter-spacing: 1px;
    text-transform: uppercase;
  }
  .back-brand-square {
    width: 26px; height: 26px;
    background: var(--green);
    border-radius: 4px;
  }
  .card-front { top: 466px; background: var(--card); }
  .brand {
    position: absolute;
    left: 56px; top: 92px;
    width: 250px;
    display: flex; flex-direction: column; align-items: center; gap: 18px;
  }
  .brand-square {
    width: 120px; height: 120px;
    background: var(--green);
    border-radius: 14px;
  }
  .brand-name {
    color: var(--green);
    font-weight: 800;
    font-size: 22px;
    letter-spacing: 1px;
    text-align: center;
    line-height: 1.2;
    text-transform: uppercase;
  }
  .divider {
    position: absolute;
    left: 344px; top: 90px;
    width: 2px; height: 200px;
    background: var(--green);
  }
  .contact {
    position: absolute;
    left: 380px; top: 92px;
    color: var(--white);
  }
  .contact-name { color: var(--green); font-weight: 700; font-size: 28px; }
  .contact-title { font-size: 15px; font-weight: 500; margin-top: 2px; color: var(--muted); }
  .contact-list { list-style: none; margin-top: 20px; font-size: 14px; line-height: 1.55; }
  .contact-list li { display: flex; align-items: flex-start; gap: 10px; }
  .contact-list svg { width: 13px; height: 13px; margin-top: 4px; flex: none; fill: var(--green); }
  .contact-list .no-icon { padding-left: 23px; }
</style>
</head>
<body>
  <section class="card card-back">
    <div class="pattern-field" role="img" aria-label="Tiled monogram pattern in glossy black and silver, fading from silver at left to black at right"></div>
    <div class="back-brand">
      <span class="back-brand-square"></span>
      <span>Ironvale</span>
    </div>
  </section>

  <section class="card card-front">
    <div class="brand">
      <div class="brand-square"></div>
      <div class="brand-name">Ironvale Construction</div>
    </div>
    <div class="divider"></div>
    <div class="contact">
      <h1 class="contact-name">Dana Whitfield</h1>
      <p class="contact-title">Owner</p>
      <ul class="contact-list">
        <li><svg viewBox="0 0 24 24"><path d="M6.6 10.8a15 15 0 0 0 6.6 6.6l2.2-2.2c.3-.3.7-.4 1-.2 1.1.4 2.3.6 3.6.6.6 0 1 .4 1 1V20c0 .6-.4 1-1 1A17 17 0 0 1 3 4c0-.6.4-1 1-1h3.5c.6 0 1 .4 1 1 0 1.3.2 2.5.6 3.6.1.3 0 .7-.2 1z"/></svg>555-210-4387</li>
        <li><svg viewBox="0 0 24 24"><path d="M2 5h20v14H2zm2 2v.5l8 5 8-5V7l-8 5z"/></svg>info@ironvalebuild.com</li>
        <li class="no-icon">www.ironvalebuild.com</li>
        <li><svg viewBox="0 0 24 24"><path d="M12 2a7 7 0 0 0-7 7c0 5 7 13 7 13s7-8 7-13a7 7 0 0 0-7-7zm0 9.5A2.5 2.5 0 1 1 12 6.5a2.5 2.5 0 0 1 0 5z"/></svg>42 Cedar Ridge Ln<br>Fairmont, MO 63000</li>
      </ul>
    </div>
  </section>
</body>
</html>
```